Website Design - TallyPorchHelpers.net

PLEASE CHECK WORD DOCUMENT ATTACHED FOR WEBSITE FLOW.

Target Market(s)

REAL ESTATE AGENTS ARE THE TARGET MARKET

Industry/Entity Type

Real Estate

Coding

Coded - Design and coding required

Number of Pages Required

4 page

Colors

Designer to choose colors to be used in the design.

Requirements
Must have
• WE LIKE RED LOGO ATTACHED
Nice to have
• PLEASE CHECK WORD DOCUMENT ATTACHED FOR WEBSITE FLOW.
Should not have

```html
<!DOCTYPE html>
<html lang="en">
<head>
<meta charset="utf-8">
<title>TallyPorchHelpers.net</title>
<link rel="stylesheet" href="https://fonts.googleapis.com/css2?family=Barlow:wght@400;500;600;700&family=Rubik:wght@500;600;700&display=swap">
<style>
:root{
  --red:#e8141b;
  --red-deep:#c90d12;
  --ink:#1d1d1d;
  --text:#555;
  --muted:#888;
  --paper:#f1f1f1;
  --plan-head:#ececec;
  --footer:#1f1f1f;
  --footer-text:#a9a9a9;
}
*{box-sizing:border-box;margin:0;padding:0}
html,body{width:718px;height:1200px;overflow:hidden}
body{position:relative;font-family:"Barlow",sans-serif;color:var(--ink);background:#fff}

/* header */
.site-header{position:absolute;left:0;top:0;width:718px;height:48px;background:#fff}
.brand{position:absolute;left:140px;top:11px;display:flex;align-items:center;gap:5px;font-weight:700;font-size:10px;line-height:11px;color:var(--red);width:80px}
.brand-mark{flex:none;width:10px;height:10px;background:var(--red)}
.main-nav{position:absolute;left:236px;top:20px;display:flex;gap:18px;font-size:6.6px;font-weight:500;letter-spacing:.3px;color:#333}
.call{position:absolute;left:492px;top:15px;display:flex;align-items:center;gap:5px}
.call small{display:block;font-size:6px;color:#666}
.call strong{display:block;font-size:9px;color:var(--red);font-weight:700}

/* hero */
.hero{position:absolute;left:0;top:48px;width:718px;height:310px;
  background:linear-gradient(100deg,#b8543a 0%,#8a5a44 30%,#5d4a3c 60%,#3f3a33 100%)}
.hero-shade{position:absolute;inset:0;background:linear-gradient(180deg,rgba(0,0,0,.05),rgba(0,0,0,.35))}
.hero-copy{position:absolute;left:0;top:127px;width:718px;text-align:center;color:#fff}
.hero-copy h1{font-family:"Rubik",sans-serif;font-weight:600;font-size:20px;letter-spacing:-.2px}
.hero-copy p{font-size:11px;font-weight:500;line-height:13.5px;margin-top:5px}

/* audience */
.audience{position:absolute;left:0;top:358px;width:718px;height:124px;background:var(--red)}
.section-title{font-family:"Rubik",sans-serif;font-weight:600;text-align:center}
.audience .section-title{position:absolute;top:29px;width:100%;color:#fff;font-size:11.5px}
.paper{position:absolute;left:0;top:482px;width:718px;height:368px;background:var(--paper)}
.option{position:absolute;top:419px;width:139px;height:87px;background:#fff;border-radius:2px;box-shadow:0 2px 6px rgba(0,0,0,.12);text-align:center;overflow:hidden}
.option svg{margin-top:14px}
.option p{font-size:7.4px;line-height:9.5px;color:#222;margin-top:4px}
.option p b{font-weight:700}
.option::after{content:"";position:absolute;left:0;bottom:0;width:100%;height:8px;background:var(--red);clip-path:polygon(0 60%,100% 0,100% 100%,0 100%)}

/* plans */
.plans-title{position:absolute;top:548px;width:718px;font-size:12px;color:#222}
.plan{position:absolute;top:581px;width:83px;height:225px;background:#fff;box-shadow:0 1px 4px rgba(0,0,0,.1);border-radius:2px;overflow:hidden}
.plan-head{height:40px;background:var(--plan-head);border-radius:0 0 50% 50%/0 0 12px 12px;text-align:center;padding-top:10px;font-family:"Rubik",sans-serif;font-size:8.4px;font-weight:600;color:#222}
.plan.featured .plan-head{background:var(--red);color:#fff}
.plan.accent .plan-head{color:var(--red)}
.plan ul{list-style:none;padding:8px 12px 0 8px}
.plan li{position:relative;padding-left:8px;font-size:6.2px;line-height:9px;color:#444;margin-bottom:8px}
.plan li svg{position:absolute;left:0;top:2px}
.plan-btn{display:block;margin:0 8px;height:19px;background:#161616;color:#fff;font-size:6.2px;font-weight:600;text-align:center;line-height:19px}
.plan.featured .plan-btn{background:var(--red)}
.plan-note{font-size:4.8px;line-height:7.5px;text-align:center;color:#777;margin-top:4px;padding:0 8px}

/* news */
.news-title{position:absolute;left:140px;top:872px;font-family:"Rubik",sans-serif;font-weight:600;font-size:12px}
.news-item{position:absolute;left:140px;width:210px;height:55px}
.news-thumb{position:absolute;left:0;top:0;width:80px;height:52px}
.news-body{position:absolute;left:91px;top:0;width:112px}
.news-body h3{font-size:8px;font-weight:500;color:#222}
.news-meta{font-size:5px;color:#777;margin-top:3px}
.news-meta b{color:var(--red);font-weight:600}
.news-body p{font-size:5.6px;line-height:9.6px;color:#666;margin-top:5px}

/* testimonials */
.testimonials{position:absolute;left:359px;top:850px;width:359px;height:190px;background:linear-gradient(90deg,var(--red) 0%,var(--red) 55%,#d42a23 100%)}
.testimonials h2{position:absolute;left:17px;top:22px;font-family:"Rubik",sans-serif;font-weight:600;font-size:12px;color:#fff}
.quote-mark{position:absolute;left:17px;top:49px}
.testimonials blockquote{position:absolute;left:34px;top:46px;width:184px;font-size:6.1px;line-height:10.5px;color:#fff}
.avatar{position:absolute;left:35px;top:135px;width:32px;height:32px;border-radius:50%;background:linear-gradient(#d9c7b8,#b39e8e);border:2px solid #fff}
.author{position:absolute;left:74px;top:140px;color:#fff}
.author b{display:block;font-size:8px;font-weight:700}
.author span{font-size:6px;padding-left:5px}
.dots{position:absolute;left:189px;top:165px;display:flex;gap:2.5px}
.dots i{width:5px;height:5px;border-radius:50%;border:1px solid #fff}
.dots i.on{background:#fff}

/* footer */
.site-footer{position:absolute;left:0;top:1040px;width:718px;height:160px;background:var(--footer);color:var(--footer-text)}
.foot-col{position:absolute;top:25px}
.foot-col h4{font-size:7px;font-weight:600;color:#fff;letter-spacing:.2px;margin-bottom:8px}
.foot-col p,.foot-col li{font-size:6px;line-height:10px}
.foot-col ul{list-style:none}
.foot-col li::before{content:"› ";}
.field{position:absolute;background:#fff;border-radius:1px;font-size:5.6px;color:#aaa;padding:4px 5px}
.send{position:absolute;left:401px;top:1136px;width:73px;height:16px;background:var(--red);color:#fff;font-size:6px;font-weight:700;text-align:center;line-height:16px}
.legal{position:absolute;top:1130px;font-size:6.4px}
</style>
</head>
<body>

<header class="site-header">
  <div class="brand"><span class="brand-mark"></span><span>Tally Porch<br>Helpers</span></div>
  <nav class="main-nav"><span>HOW IT WORKS</span><span>SERVICE AREA</span><span>PRICING</span><span>ABOUT US</span><span>FAQ</span></nav>
  <div class="call">
    <svg width="16" height="16" viewBox="0 0 24 24" fill="none" stroke="#e8141b" stroke-width="2"><path d="M5 3h4l2 5-3 2a12 12 0 0 0 6 6l2-3 5 2v4a2 2 0 0 1-2 2A18 18 0 0 1 3 5a2 2 0 0 1 2-2z"/></svg>
    <div><small>Call Us Today</small><strong>1800 555 0142</strong></div>
  </div>
</header>

<section class="hero" role="img" aria-label="Photo of a couple meeting an agent outside a house with an open house sign">
  <div class="hero-shade"></div>
  <div class="hero-copy">
    <h1>Helping agents save time and money.</h1>
    <p>We place signs and boost foot traffic to your open houses<br>using proven marketing techniques.</p>
  </div>
</section>

<section class="audience"><h2 class="section-title">Choose The Option Below That Best Describes You</h2></section>
<div class="paper"></div>

<div class="option" style="left:140px">
  <svg width="24" height="26" viewBox="0 0 24 26" fill="#e8141b"><circle cx="12" cy="7" r="6"/><path d="M1 26a11 10 0 0 1 22 0z"/></svg>
  <p>I'M A<br><b>FULL ON BROKERAGE</b></p>
</div>
<div class="option" style="left:290px">
  <svg width="28" height="26" viewBox="0 0 28 26" fill="#e8141b"><circle cx="14" cy="5" r="4"/><circle cx="6" cy="9" r="3.5"/><circle cx="22" cy="9" r="3.5"/><path d="M8 20a6 7 0 0 1 12 0z"/><path d="M0 22a6 7 0 0 1 11-3v3z"/><path d="M28 22a6 7 0 0 0-11-3v3z"/><rect x="8" y="18" width="12" height="6"/></svg>
  <p>I'M AN<br><b>IND. BROKER WITH A TEAM</b></p>
</div>
<div class="option" style="left:439px">
  <svg width="24" height="26" viewBox="0 0 24 26" fill="#e8141b"><rect x="1" y="0" width="3" height="26"/><rect x="20" y="0" width="3" height="26"/><rect x="4" y="2" width="16" height="8"/></svg>
  <p>I NEED<br><b>SIGN PLACEMENT ASAP</b></p>
</div>

<h2 class="section-title plans-title">Choose Your Package</h2>

<svg width="0" height="0" style="position:absolute"><defs><symbol id="tick" viewBox="0 0 10 10"><path d="M1 5l3 3 5-7" fill="none" stroke="#e8141b" stroke-width="1.8"/></symbol></defs></svg>

<div class="plan" style="left:140px"><div class="plan-head">5 SIGNS</div>
  <ul><li><svg width="6" height="6"><use href="#tick"/></svg>Place signs strategically in best areas according to where the open house is located</li><li><svg width="6" height="6"><use href="#tick"/></svg>Pick Up the signs after the open house</li><li><svg width="6" height="6"><use href="#tick"/></svg>Store custom signs for you if needed</li></ul>
  <span class="plan-btn">SIGN UP</span><p class="plan-note">Sign Up For A Subscription And Get These Marketing Services For Free</p></div>
<div class="plan" style="left:228px"><div class="plan-head">10 SIGNS</div>
  <ul><li><svg width="6" height="6"><use href="#tick"/></svg>Place signs strategically in best areas according to where the open house is located</li><li><svg width="6" height="6"><use href="#tick"/></svg>Pick Up the signs after the open house</li><li><svg width="6" height="6"><use href="#tick"/></svg>Store custom signs for you if needed</li></ul>
  <span class="plan-btn">SIGN UP</span><p class="plan-note">Sign Up For A Subscription And Get These Marketing Services For Free</p></div>
<div class="plan featured" style="left:317px"><div class="plan-head">15 SIGNS</div>
  <ul><li><svg width="6" height="6"><use href="#tick"/></svg>Place signs strategically in best areas according to where the open house is located</li><li><svg width="6" height="6"><use href="#tick"/></svg>Pick Up the signs after the open house</li><li><svg width="6" height="6"><use href="#tick"/></svg>Store custom signs for you if needed</li></ul>
  <span class="plan-btn">SIGN UP</span><p class="plan-note">Sign Up For A Subscription And Get These Marketing Services For Free</p></div>
<div class="plan" style="left:406px"><div class="plan-head">20 SIGNS</div>
  <ul><li><svg width="6" height="6"><use href="#tick"/></svg>Place signs strategically in best areas according to where the open house is located</li><li><svg width="6" height="6"><use href="#tick"/></svg>Pick Up the signs after the open house</li><li><svg width="6" height="6"><use href="#tick"/></svg>Store custom signs for you if needed</li></ul>
  <span class="plan-btn">SIGN UP</span><p class="plan-note">Sign Up For A Subscription And Get These Marketing Services For Free</p></div>
<div class="plan accent" style="left:494px"><div class="plan-head">25 SIGNS</div>
  <ul><li><svg width="6" height="6"><use href="#tick"/></svg>Place signs strategically in best areas according to where the open house is located</li><li><svg width="6" height="6"><use href="#tick"/></svg>Pick Up the signs after the open house</li><li><svg width="6" height="6"><use href="#tick"/></svg>Store custom signs for you if needed</li></ul>
  <span class="plan-btn">SIGN UP</span><p class="plan-note">Sign Up For A Subscription And Get These Marketing Services For Free</p></div>

<h2 class="news-title">Latest News</h2>
<article class="news-item" style="top:897px">
  <div class="news-thumb" role="img" aria-label="Photo of a red open house sign on a lawn" style="background:linear-gradient(135deg,#c8211d,#8e5d3a 60%,#6f8a4a)"></div>
  <div class="news-body"><h3>Lorem Ipsum charsets layouts</h3><p class="news-meta">By <b>Mara Quill</b> | 03 Aug 2018</p><p>Class aptent taciti sociosqu ad litora torquent per conubia himenaeos. Mauris in erat justo.</p></div>
</article>
<article class="news-item" style="top:965px">
  <div class="news-thumb" role="img" aria-label="Photo of an agent greeting a couple at a doorway" style="background:linear-gradient(135deg,#c9d3dc,#8d99a8 55%,#5d6a7c)"></div>
  <div class="news-body"><h3>Lorem Ipsum charsets layouts</h3><p class="news-meta">By <b>Mara Quill</b> | 03 Aug 2018</p><p>Class aptent taciti sociosqu ad litora torquent per conubia himenaeos. Mauris in erat justo.</p></div>
</article>

<section class="testimonials" role="img" aria-label="Red-tinted portrait backdrop for testimonials">
  <h2>Testimonials</h2>
  <svg class="quote-mark" width="12" height="9" viewBox="0 0 12 9" fill="none" stroke="#fff" stroke-width="1"><path d="M5 1C2 2 1 4 1 6a2 2 0 1 0 2-2M11 1C8 2 7 4 7 6a2 2 0 1 0 2-2"/></svg>
  <blockquote>Class aptent taciti sociosqu ad litora torquent per conubia nostra, per inceptos himenaeos. Mauris in condimentum sit amet a augue. Sed non neque elit. Sed ut imperdiet nisi. Proin condimentum fermentum nunc. Etiam pharetra, erat sed fermentum feugiat, velit mauris egestas quam, ut aliquam massa nisl quis neque. Suspendisse in orci enim. Mauris in condimentum sit amet a augue. Sed non fermentum feugiat, velit mauris egestas quam, neque elit.</blockquote>
  <div class="avatar" role="img" aria-label="Client portrait"></div>
  <div class="author"><b>- Ezra Lund</b><span>Lorem ipsum dolor</span></div>
  <div class="dots"><i class="on"></i><i></i><i></i><i></i><i></i></div>
</section>

<footer class="site-footer">
  <div class="foot-col" style="left:140px"><h4>CONTACT INFORMATION</h4>
    <p>412 Brindle Lane,<br>Suite 20, Harlow, TX 75000</p>
    <p style="margin-top:8px">Phone: 1800 555 0142<br>Fax: 1800 555 0168<br>info@tallyporchhelpers.net</p></div>
  <div class="foot-col" style="left:252px"><h4>QUICK LINKS</h4>
    <ul><li>How It Works</li><li>Service Area</li><li>Pricing</li><li>About Us</li><li>FAQ</li></ul></div>
  <div class="foot-col" style="left:326px"><h4>SOCIAL MEDIA</h4>
    <ul><li>Friendwall</li><li>Chirpline</li><li>WorkLinkr</li><li>Reelhub</li><li>Snapgrid</li></ul></div>
  <div class="foot-col" style="left:401px"><h4>QUICK CONTACT</h4></div>
  <div class="legal" style="left:140px">Copyright © 2018 Tally Porch Helpers</div>
  <div class="legal" style="left:478px">Terms of Use | Privacy | Sitemap</div>
</footer>
<div class="field" style="left:401px;top:1080px;width:87px;height:17px">Name</div>
<div class="field" style="left:490px;top:1080px;width:87px;height:17px">Email</div>
<div class="field" style="left:401px;top:1099px;width:176px;height:34px">Message</div>
<div class="send">SEND A MESSAGE</div>

</body>
</html>
```